Blow Dry Bar Business Cards

These cards must be eye catching and modern.
You must be willing to work fast and make changes.

Winner will be offered other projects

Files 1 THIS IS THE STYLE CARDS I AM INTRESTED IN!!!
Please be creative, I am paying for my own eye catching design. I need files to be nexa press ready.

COLORS THAT ARE PAINTED INSIDE MY SHOP:
- - - http://www.quorvelpaint.example/en/explore-colors/painter/color-selector.html?colors=4007-3C

- - - http://www.brandivex.example/color/paint-colors/hidden-corridor-d58-2

I want the business cards sleek and modern if you use the logo please correct imperfections. I added the part that says Blow Dry Bar (see website).
Do not be afraid to separate the blow dryer from the name to make the cards look like the file with the pink elephant.

SHOULD INCLUDE
*Blow Dryer (we are a blow dry bar not a salon we do not cut or color so do not include sheers of any kind)
*BUSINESS NAME: Simply Swept Upward - Blow Dry Bar (PLEASE SEE MY WEBSITE)
* Website: SIMPLYSWEPTUPWARD.EXAMPLE
*Phone number (555) 014-2763
Updates

Nexa press said it can be submitted in JPG

http://www.brandivex.example/color/paint-colors/hidden-corridor-d58-2 http://www.quorvelpaint.example/en/explore-colors/painter/color-selector.html?colors=4007-3C ^^^^ These links will take you to the color paint that is painted inside my shop.

Target Market(s)

AGES 18 - 55 WOMEN
HIGH END MARKET

Industry/Entity Type

Salon

Requirements
Must have
• SEE COLOR EXAMPLE FILE
BLOW DRYER
UNIQUE
I LIKE THE CARD WITH THE PINK ELEPHANT THE BEST
Nice to have
• BE AS CREATIVE AND MODERN AS POSSIBLE DO NOT COPY ANY OF THE CARDS BELOW.
Should not have
• SCISSORS
PINK

```html
<!DOCTYPE html>
<html lang="en">
<head>
<meta charset="utf-8">
<title>Swept Upward – Blow Dry Bar Business Cards</title>
<link rel="stylesheet" href="https://fonts.googleapis.com/css2?family=Josefin+Slab:wght@400;600&family=Lato:wght@400;700&display=swap">
<style>
  :root {
    --bg: #ece7df;
    --teal: #5cc4cb;
    --teal-deep: #3fb1b9;
    --teal-light: #8fd8dd;
    --white: #ffffff;
    --ink: #3a2a28;
    --brown: #5a3a35;
    --shadow: rgba(40, 30, 20, 0.22);
  }
  * { margin: 0; padding: 0; box-sizing: border-box; }
  html, body { width: 1200px; height: 1023px; overflow: hidden; }
  body {
    background: var(--bg);
    font-family: "Lato", Arial, sans-serif;
    position: relative;
  }
  .card {
    position: absolute;
    left: 190px;
    width: 820px;
    height: 469px;
    border-radius: 28px;
    overflow: hidden;
    box-shadow: 0 10px 28px var(--shadow);
  }
  .card-front { top: 30px; background: var(--white); }
  .card-back {
    top: 524px;
    background: linear-gradient(160deg, var(--teal-light) 0%, var(--teal) 45%, var(--teal-deep) 100%);
  }
  .front-swoosh { position: absolute; inset: 0; width: 100%; height: 100%; }

  .owner {
    position: absolute;
    left: 70px;
    top: 300px;
    color: var(--ink);
  }
  .owner-name { font-size: 30px; font-weight: 400; }
  .owner-role { font-size: 22px; margin-top: 4px; padding-left: 14px; }

  .brand {
    position: absolute;
    right: 60px;
    top: 170px;
    text-align: right;
  }
  .brand-mark {
    display: flex;
    align-items: center;
    justify-content: flex-end;
    gap: 18px;
  }
  .brand-dot {
    width: 40px; height: 40px;
    border-radius: 50%;
    background: var(--teal);
  }
  .brand-name {
    font-family: "Josefin Slab", Georgia, serif;
    font-weight: 400;
    font-size: 76px;
    line-height: 1;
    color: var(--teal);
  }
  .brand-tagline {
    font-family: "Josefin Slab", Georgia, serif;
    font-weight: 600;
    font-size: 36px;
    color: var(--brown);
    margin-top: 14px;
  }
  .brand-service {
    font-family: "Josefin Slab", Georgia, serif;
    font-weight: 600;
    font-size: 26px;
    color: var(--brown);
    margin-top: 2px;
  }

  .back-brand {
    position: absolute;
    right: 70px;
    top: 70px;
    display: flex;
    align-items: center;
    gap: 16px;
  }
  .back-brand .brand-name { color: var(--white); font-size: 62px; }
  .back-brand .brand-dot { background: var(--white); width: 34px; height: 34px; }

  .contact {
    position: absolute;
    left: 60px;
    bottom: 60px;
    color: var(--ink);
    list-style: none;
  }
  .contact li {
    display: flex;
    align-items: center;
    gap: 12px;
    font-size: 27px;
    line-height: 1.55;
  }
  .contact-address { font-size: 28px; }
  .contact svg { width: 22px; height: 22px; flex: none; }
  .contact-web { letter-spacing: 0.5px; }
</style>
</head>
<body>

  <section class="card card-front" aria-label="Business card front">
    <svg class="front-swoosh" viewBox="0 0 820 469" preserveAspectRatio="none" aria-hidden="true">
      <defs>
        <linearGradient id="swooshTeal" x1="0" y1="0" x2="1" y2="1">
          <stop offset="0" stop-color="#8fd8dd"/>
          <stop offset="1" stop-color="#4dbac2"/>
        </linearGradient>
      </defs>
      <!-- top band curving down the left side -->
      <path d="M0 0 H430 C330 20 250 80 215 170 C190 235 110 255 0 250 Z" fill="url(#swooshTeal)"/>
      <!-- lower left lobe -->
      <path d="M0 469 V285 C120 270 240 240 300 200 C260 300 220 420 330 469 Z" fill="url(#swooshTeal)"/>
      <!-- light accent line between shapes -->
      <path d="M0 268 C120 262 230 232 300 198" stroke="#d8f1f3" stroke-width="8" fill="none"/>
    </svg>

    <div class="owner">
      <p class="owner-name">Mara Ellison</p>
      <p class="owner-role">Owner</p>
    </div>

    <div class="brand">
      <div class="brand-mark">
        <span class="brand-dot"></span>
        <span class="brand-name">Swept Upward</span>
      </div>
      <p class="brand-tagline">Simply Swept Upward</p>
      <p class="brand-service">Blow Dry Bar</p>
    </div>
  </section>

  <section class="card card-back" aria-label="Business card back">
    <div class="back-brand">
      <span class="brand-name">Swept Upward</span>
      <span class="brand-dot"></span>
    </div>

    <ul class="contact">
      <li class="contact-address">482 Harbor Reed Lane Suite 7 Port Alden, texas 77000</li>
      <li class="contact-phone">
        <svg viewBox="0 0 24 24" aria-hidden="true"><path fill="#3a2a28" d="M6.6 10.8a15.1 15.1 0 0 0 6.6 6.6l2.2-2.2c.3-.3.7-.4 1-.2 1.1.4 2.3.6 3.6.6.6 0 1 .4 1 1V20c0 .6-.4 1-1 1A17 17 0 0 1 3 4c0-.6.4-1 1-1h3.5c.6 0 1 .4 1 1 0 1.3.2 2.5.6 3.6.1.3 0 .7-.2 1z"/></svg>
        (555) 014-2763
      </li>
      <li class="contact-web">
        <svg viewBox="0 0 24 24" aria-hidden="true"><circle cx="12" cy="12" r="10" fill="#3a2a28"/><path d="M2 12h20M12 2c3 3 3 17 0 20M12 2c-3 3-3 17 0 20" stroke="#5cc4cb" stroke-width="1.4" fill="none"/></svg>
        WWW.SIMPLYSWEPTUPWARD.EXAMPLE
      </li>
    </ul>
  </section>

</body>
</html>
```